Dorvik Electric Ltd

Looking for a single page website and Facebook page design. I am an electrical contractor based on Vancouver Island. I do service, custom homes, residential and commercial installations. My company just started out, so I don't have any pictures of installs yet. I have 25 years experience. I would like the colors to be my logo colors black and I have a black Brandt Halvard that will be my vehicle which I will have a wrap for.
Updates

I just posted the contest today, not sure why the deadline is the same day.

Industry/Entity Type

Electrician

Requirements
Must have
• Services provided, About me section, quote section,
Nice to have
• I am not quite sure yet, I need to see some designs first .

```html
<!DOCTYPE html>
<html lang="en">
<head>
<meta charset="utf-8">
<title>Dorvik Electric Ltd</title>
<link href="https://fonts.googleapis.com/css2?family=Montserrat:wght@500;600;700;800&family=Open+Sans:wght@400;600;700&display=swap" rel="stylesheet">
<style>
:root{
  --yellow:#f6b500;
  --yellow-deep:#e9a400;
  --black:#0e0e0e;
  --dark:#1d1f22;
  --ink:#222;
  --muted:#555;
  --white:#fff;
  --card-line:#d8d8d8;
}
*{box-sizing:border-box;margin:0;padding:0}
html,body{width:1200px;height:4428px;overflow:hidden}
body{position:relative;background:var(--white);font-family:"Open Sans",Arial,sans-serif;color:var(--ink)}
.abs{position:absolute}
h1,h2,h3,.nav a,.btn,.brand{font-family:"Montserrat",Arial,sans-serif}
.accent{color:var(--yellow)}

/* top bar */
.topbar{left:0;top:0;width:1200px;height:48px;background:var(--black)}
.topbar .social{left:72px;top:14px;display:flex;gap:18px}
.social span{display:block;width:20px;height:20px;border-radius:50%;background:var(--white)}
.topbar .contact-strip{right:0;top:0;width:520px;height:48px;background:var(--yellow);clip-path:polygon(40px 0,100% 0,100% 100%,0 100%);display:flex;align-items:center;gap:30px;padding-left:78px;font-size:15px;font-weight:600;color:var(--black)}
.contact-strip .item{display:flex;align-items:center;gap:8px}

/* nav */
.site-header{left:0;top:48px;width:1200px;height:128px;background:var(--white)}
.brand{display:flex;align-items:center;gap:10px;font-weight:800;font-size:17px;letter-spacing:.5px;color:var(--black)}
.site-header .brand{left:72px;top:44px}
.brand .dot{width:38px;height:38px;border-radius:50%;border:3px solid var(--yellow)}
.nav{left:356px;top:64px;display:flex;gap:34px}
.nav a{font-size:15px;font-weight:700;color:var(--black);text-decoration:none}
.nav a.active{color:var(--yellow)}

/* hero */
.hero{left:0;top:176px;width:1200px;height:644px;background:linear-gradient(90deg,#1a1a1a 0%,#2d2a26 35%,#6b5a45 62%,#a89478 82%,#cbbfad 100%)}
.hero h1{left:72px;top:324px;font-size:50px;font-weight:800;color:var(--white);letter-spacing:.5px}
.hero .lead{left:72px;top:392px;width:520px;font-family:"Montserrat",Arial,sans-serif;font-size:25px;font-weight:700;line-height:1.3;color:var(--white)}
.btn{display:inline-block;font-weight:700;font-size:15px;border-radius:30px;text-align:center;text-decoration:none}
.btn-yellow{background:var(--yellow);color:var(--black);padding:14px 36px}
.btn-black{background:var(--black);color:var(--white);padding:14px 40px}
.btn-outline{border:1.5px solid #333;color:var(--black);padding:8px 26px;font-size:14px;font-weight:600}
.hero .btn{left:72px;top:500px}
.dots{display:flex;gap:10px}
.dots span{width:12px;height:12px;border-radius:50%;background:var(--white);opacity:.55}
.dots span.on{opacity:1}
.hero .dots{left:564px;top:578px}

/* welcome */
.welcome-mark{left:110px;top:870px;width:440px;height:440px;border-radius:50%;border:14px solid var(--yellow);display:flex;align-items:center;justify-content:center}
.welcome-mark .brand{font-size:34px}
.welcome-copy{left:616px;top:886px;width:510px}
.welcome-copy h2{font-size:32px;font-weight:800;line-height:1.2;color:var(--black)}
.welcome-copy p{margin:22px 0 40px;font-size:16px;line-height:1.62;color:var(--ink)}

/* services */
.services{left:0;top:1396px;width:1200px;height:650px;background:linear-gradient(180deg,#2a2622 0%,#1b1917 100%)}
.section-title{width:1200px;text-align:center;font-size:36px;font-weight:800;left:0}
.services .section-title{top:76px;color:var(--white)}
.cards{left:72px;display:flex;gap:48px}
.services .cards{top:160px}
.card{width:312px;border-radius:22px;overflow:hidden;background:var(--white)}
.card .photo{height:200px}
.card .body{padding:18px 22px 22px;border-radius:22px 22px 0 0;margin-top:-20px;background:var(--white);position:relative}
.card h3{font-size:20px;font-weight:800;color:var(--yellow);line-height:1.2;margin-bottom:8px}
.card p{font-size:14px;line-height:1.55;color:var(--muted);margin-bottom:16px}
.services .card{height:400px}
.ph-warm{background:linear-gradient(135deg,#9a8670,#d9cdbb)}
.ph-cool{background:linear-gradient(135deg,#7b8a9a,#d6dde4)}
.ph-brick{background:linear-gradient(135deg,#8c6248,#d7c0a8)}

/* gallery */
.gallery .section-title{top:2148px;color:var(--black)}
.tile{position:absolute}

/* testimonials */
.testimonials{left:0;top:2780px;width:1200px;height:700px;background:linear-gradient(180deg,#26231f,#35302a 50%,#1c1a18)}
.testimonials .section-title{top:120px;color:var(--white)}
.quote-card{position:absolute;top:200px;width:516px;height:250px;background:var(--white);border-radius:20px;padding:34px 120px 30px 30px;border-bottom:8px solid var(--yellow)}
.quote-card p{font-size:15px;line-height:1.6;font-style:italic;color:var(--ink)}
.quote-card .name{margin-top:18px;font-family:"Montserrat",Arial,sans-serif;font-weight:700;font-size:15px;color:var(--yellow)}
.quote-card .avatar{position:absolute;right:30px;top:30px;width:78px;height:78px;border-radius:50%;background:linear-gradient(135deg,#c7b6a2,#8a7966)}
.dash{display:flex;gap:12px}
.dash span{width:32px;height:5px;background:var(--white);opacity:.6;border-radius:3px}
.dash span.on{opacity:1}
.testimonials .dash{left:522px;top:560px}

/* blog */
.blog .section-title{top:3540px;color:var(--black)}
.blog .cards{top:3620px}
.blog .card{height:420px;border:1px solid var(--card-line)}
.blog .date{font-size:13px;font-weight:700;color:var(--yellow);margin-bottom:6px}
.blog .card p{font-size:17px;color:var(--ink)}

/* footer */
.footer{left:0;top:4160px;width:1200px;height:268px;background:var(--black);color:var(--white)}
.footer .brand{color:var(--white);left:72px;top:72px;font-size:16px}
.footer .copy{left:72px;top:130px;font-size:12px;color:#bbb;line-height:1.5}
.f-col{position:absolute;top:46px;display:flex;gap:12px}
.f-col .ico{width:30px;height:30px;border-radius:50%;background:var(--yellow);flex:none;display:flex;align-items:center;justify-content:center}
.f-col h3{font-size:17px;font-weight:700;margin-bottom:6px}
.f-col p{font-size:13px;line-height:1.45;color:#ddd}
.footer .social{display:flex;gap:14px;margin-top:10px}
.footer .social span{width:24px;height:24px}
.footer-nav{left:356px;top:222px;display:flex;gap:34px}
.footer-nav a{color:var(--white);font-size:13px;font-weight:700;text-decoration:none}
</style>
</head>
<body>

<!-- top bar -->
<div class="abs topbar">
  <div class="abs social" aria-label="Social links"><span></span><span></span><span></span><span></span></div>
  <div class="abs contact-strip">
    <div class="item">
      <svg width="18" height="18" viewBox="0 0 24 24" aria-hidden="true"><path fill="#0e0e0e" d="M6.6 10.8a15 15 0 006.6 6.6l2.2-2.2a1 1 0 011-.25 11.4 11.4 0 003.6.57 1 1 0 011 1V20a1 1 0 01-1 1A17 17 0 013 4a1 1 0 011-1h3.5a1 1 0 011 1c0 1.25.2 2.45.57 3.57a1 1 0 01-.25 1z"/></svg>
      1-800-555-0187
    </div>
    <div class="item">
      <svg width="18" height="14" viewBox="0 0 24 18" aria-hidden="true"><rect x="1" y="1" width="22" height="16" rx="2" fill="none" stroke="#0e0e0e" stroke-width="2"/><path d="M1 2l11 8 11-8" fill="none" stroke="#0e0e0e" stroke-width="2"/></svg>
      info@dorvikelectric.ca
    </div>
  </div>
</div>

<!-- header -->
<header class="abs site-header">
  <div class="abs brand"><span class="dot"></span>DORVIK ELECTRIC LTD</div>
  <nav class="abs nav">
    <a class="active" href="#">HOME</a><a href="#">ABOUT US</a><a href="#">SERVICES</a><a href="#">GALLERY</a><a href="#">TESTIMONIALS</a><a href="#">BLOG</a><a href="#">CONTACT US</a>
  </nav>
</header>

<!-- hero -->
<section class="abs hero" role="img" aria-label="Smiling electrician in a white hard hat and safety glasses working on wiring">
  <h1 class="abs">DORVIK <span class="accent">ELECTRIC</span> LTD</h1>
  <p class="abs lead">I am an electrical contractor based on Vancouver Island.</p>
  <a class="abs btn btn-yellow" href="#">READ MORE</a>
  <div class="abs dots"><span class="on"></span><span></span><span></span><span></span></div>
</section>

<!-- welcome -->
<section>
  <div class="abs welcome-mark"><div class="brand">DORVIK ELECTRIC LTD</div></div>
  <div class="abs welcome-copy">
    <h2>WELCOME TO<br><span class="accent">DORVIK ELECTRIC LTD</span></h2>
    <p>Sed ut perspiciatis unde omnis iste natus error sit voluptatem accusantium doloremque laudantium, totam rem aperiam, eaque ipsa quae ab illo inventore veritatis et quasi architecto beatae vitae dicta sunt explicabo. Nemo enim ipsam voluptatem quia voluptas sit aut odit aut fugit, sed quia consequuntur magni dolores eos qui ratione voluptatem.</p>
    <a class="btn btn-black" href="#">READ MORE</a>
  </div>
</section>

<!-- services -->
<svg class="abs" style="left:0;top:1370px" width="1200" height="90" viewBox="0 0 1200 90" aria-hidden="true">
  <path d="M0 26 Q600 -20 1200 26 L1200 90 L0 90Z" fill="#2a2622"/>
  <path d="M0 26 Q600 -20 1200 26" fill="none" stroke="#f6b500" stroke-width="6"/>
</svg>
<section class="abs services">
  <h2 class="abs section-title">OUR <span class="accent">SERVICES</span></h2>
  <div class="abs cards">
    <article class="card">
      <div class="photo ph-cool" role="img" aria-label="Electrician in a hard hat working at a breaker panel"></div>
      <div class="body"><h3>CUSTOM HOMES</h3><p>Sed ut perspiciatis unde omnis iste natus error sit voluptatem accusantium omnis.</p><a class="btn btn-outline" href="#">Read More</a></div>
    </article>
    <article class="card">
      <div class="photo ph-warm" role="img" aria-label="Electrician fitting wiring in a residential ceiling"></div>
      <div class="body"><h3>RESIDENTIAL</h3><p>Sed ut perspiciatis unde omnis iste natus error sit voluptatem accus antium ultamco.</p><a class="btn btn-outline" href="#">Read More</a></div>
    </article>
    <article class="card">
      <div class="photo ph-brick" role="img" aria-label="Electrician installing fixtures in a commercial space with brick walls"></div>
      <div class="body"><h3>COMMERCIAL<br>INSTALLATIONS</h3><p>Sed ut perspiciatis unde omnis iste natus error sit voluptatem accusac.</p><a class="btn btn-outline" href="#">Read More</a></div>
    </article>
  </div>
</section>
<svg class="abs" style="left:0;top:2010px" width="1200" height="70" viewBox="0 0 1200 70" aria-hidden="true">
  <path d="M0 0 L1200 0 L1200 20 Q600 70 0 20Z" fill="#1b1917"/>
  <path d="M0 20 Q600 70 1200 20" fill="none" stroke="#f6b500" stroke-width="6"/>
</svg>

<!-- gallery -->
<section class="gallery">
  <h2 class="abs section-title">PROJECT <span class="accent">GALLERY</span></h2>
  <div class="tile ph-warm" style="left:0;top:2352px;width:282px;height:208px" role="img" aria-label="Electrician fitting a ceiling light"></div>
  <div class="tile ph-cool" style="left:292px;top:2232px;width:300px;height:216px" role="img" aria-label="Electrician on a ladder installing ceiling fixtures"></div>
  <div class="tile ph-warm" style="left:608px;top:2232px;width:300px;height:216px" role="img" aria-label="Electrician kneeling to wire an outlet"></div>
  <div class="tile ph-cool" style="left:292px;top:2460px;width:300px;height:220px" role="img" aria-label="Electrician in overalls working at a wall panel"></div>
  <div class="tile ph-brick" style="left:608px;top:2460px;width:300px;height:220px" role="img" aria-label="Interior of a commercial space under electrical installation"></div>
  <div class="tile ph-cool" style="left:916px;top:2340px;width:236px;height:220px" role="img" aria-label="Electrician in a yellow hard hat checking a switchboard"></div>
</section>

<!-- testimonials -->
<svg class="abs" style="left:0;top:2750px" width="1200" height="90" viewBox="0 0 1200 90" aria-hidden="true">
  <path d="M0 30 Q600 -20 1200 30 L1200 90 L0 90Z" fill="#26231f"/>
  <path d="M0 30 Q600 -20 1200 30" fill="none" stroke="#f6b500" stroke-width="6"/>
</svg>
<section class="abs testimonials" role="img" aria-label="Dimmed background of a home under construction">
  <h2 class="abs section-title">CUSTOMER <span class="accent">TESTIMONIALS</span></h2>
  <div class="quote-card" style="left:72px">
    <p>“ Sed ut perspiciatis unde omnis iste natus error sit voluptatem accusantium doloremque laudantium, totam rem aperiam, eaque ipsa quae ab illo inventore veritatis et quasi architecto beatae vitae.”</p>
    <div class="name">Name Heading</div>
    <div class="avatar" role="img" aria-label="Customer portrait"></div>
  </div>
  <div class="quote-card" style="left:612px">
    <p>“ Sed ut perspiciatis unde omnis iste natus error sit voluptatem accusantium doloremque laudantium, totam rem aperiam, eaque ipsa quae ab illo inventore veritatis et quasi architecto beatae vitae.”</p>
    <div class="name">Name Heading</div>
    <div class="avatar" role="img" aria-label="Customer portrait"></div>
  </div>
  <div class="abs dash"><span class="on"></span><span></span><span></span><span></span></div>
</section>
<svg class="abs" style="left:0;top:3440px" width="1200" height="70" viewBox="0 0 1200 70" aria-hidden="true">
  <path d="M0 0 L1200 0 L1200 20 Q600 70 0 20Z" fill="#1c1a18"/>
  <path d="M0 20 Q600 70 1200 20" fill="none" stroke="#f6b500" stroke-width="6"/>
</svg>

<!-- blog -->
<section class="blog">
  <h2 class="abs section-title">BLOG <span class="accent">ARTICLES</span></h2>
  <div class="abs cards">
    <article class="card">
      <div class="photo ph-warm" role="img" aria-label="Electrician testing a circuit with a multimeter"></div>
      <div class="body"><div class="date">June 18, 2020</div><p>Sed ut perspiciatis unde omnis iste natus error sit voluptatem accusantium</p><a class="btn btn-outline" href="#">Read More</a></div>
    </article>
    <article class="card">
      <div class="photo ph-cool" role="img" aria-label="Electrician on a ladder in an open room"></div>
      <div class="body"><div class="date">June 18, 2020</div><p>Sed ut perspiciatis unde omnis iste natus error sit voluptatem accusantium</p><a class="btn btn-outline" href="#">Read More</a></div>
    </article>
    <article class="card">
      <div class="photo ph-brick" role="img" aria-label="Electrician wiring a light fixture near a window"></div>
      <div class="body"><div class="date">June 18, 2020</div><p>Sed ut perspiciatis unde omnis iste natus error sit voluptatem accusantium</p><a class="btn btn-outline" href="#">Read More</a></div>
    </article>
  </div>
</section>

<!-- footer -->
<svg class="abs" style="left:0;top:4130px" width="1200" height="60" viewBox="0 0 1200 60" aria-hidden="true">
  <path d="M0 40 Q600 -10 1200 40 L1200 60 L0 60Z" fill="#0e0e0e"/>
  <path d="M0 40 Q600 -10 1200 40" fill="none" stroke="#f6b500" stroke-width="6"/>
</svg>
<footer class="abs footer">
  <div class="abs brand"><span class="dot"></span>DORVIK ELECTRIC LTD</div>
  <p class="abs copy">© 2022 Dorvik Electric Ltd<br>All rights reserved.</p>
  <div class="f-col" style="left:346px">
    <span class="ico"><svg width="14" height="18" viewBox="0 0 14 20" aria-hidden="true"><path fill="#0e0e0e" d="M7 0a7 7 0 00-7 7c0 5 7 13 7 13s7-8 7-13a7 7 0 00-7-7zm0 9.5A2.5 2.5 0 117 4.5a2.5 2.5 0 010 5z"/></svg></span>
    <div><h3>Address</h3><p>Tempoibus autem qui<br>busdam et aut</p></div>
  </div>
  <div class="f-col" style="left:620px">
    <span class="ico"><svg width="16" height="16" viewBox="0 0 24 24" aria-hidden="true"><path fill="#0e0e0e" d="M6.6 10.8a15 15 0 006.6 6.6l2.2-2.2a1 1 0 011-.25 11.4 11.4 0 003.6.57 1 1 0 011 1V20a1 1 0 01-1 1A17 17 0 013 4a1 1 0 011-1h3.5a1 1 0 011 1c0 1.25.2 2.45.57 3.57a1 1 0 01-.25 1z"/></svg></span>
    <div><h3>Contact Us</h3><p>1-800-555-0187<br>info@dorvikelectric.ca</p></div>
  </div>
  <div class="f-col" style="left:920px">
    <div><h3>Follow Us</h3><div class="social"><span></span><span></span><span></span><span></span></div></div>
  </div>
  <nav class="abs footer-nav">
    <a href="#">HOME</a><a href="#">ABOUT US</a><a href="#">SERVICES</a><a href="#">GALLERY</a><a href="#">TESTIMONIALS</a><a href="#">BLOG</a><a href="#">CONTACT US</a>
  </nav>
</footer>

</body>
</html>
```